Harrow Grading LLC business card design

Excavation company business cards

Contact Information for Business Card

Harrow Grading LLC cell phone 208-417-6290 office phone 208-319-4856 harrowgradingllc@maplecove.com Driveways, site prep, retaining walls, septic systems, rock delivery

Colors

Designer to choose colors to be used in the design.

```html
<!DOCTYPE html>
<html lang="en">
<head>
<meta charset="utf-8">
<title>Harrow Grading LLC – Business Card</title>
<link href="https://fonts.googleapis.com/css2?family=Roboto:wght@400;700;900&display=swap" rel="stylesheet">
<style>
  :root {
    --backdrop: #2a2a2a;
    --card: #1c1c1c;
    --orange: #ee7222;
    --white: #ffffff;
  }
  * { margin: 0; padding: 0; box-sizing: border-box; }
  html, body { width: 1200px; height: 1200px; overflow: hidden; }
  body {
    background: var(--backdrop);
    font-family: "Roboto", Arial, sans-serif;
    position: relative;
  }
  .card {
    position: absolute;
    top: 250px;
    width: 400px;
    height: 700px;
    background: var(--card);
    border-radius: 26px;
    box-shadow: 0 18px 40px rgba(0,0,0,.45);
    color: var(--white);
    text-align: center;
  }
  .card--front { left: 160px; }
  .card--back { left: 640px; }

  .brand {
    position: absolute;
    left: 0; right: 0;
    display: flex;
    align-items: center;
    justify-content: center;
    gap: 12px;
    color: var(--orange);
    font-weight: 900;
    font-size: 30px;
    letter-spacing: .5px;
    text-transform: uppercase;
  }
  .brand__mark {
    width: 22px; height: 22px;
    background: var(--orange);
  }
  .card--front .brand { top: 150px; }
  .card--back .brand { top: 235px; }

  .person { position: absolute; top: 365px; left: 0; right: 0; }
  .person__name {
    color: var(--orange);
    font-weight: 700;
    font-size: 30px;
    letter-spacing: .5px;
    text-transform: uppercase;
  }
  .person__role { font-size: 21px; margin-top: 2px; }

  .icon-rule {
    position: absolute;
    top: 470px; left: 40px; right: 40px;
    display: flex; align-items: center; gap: 14px;
  }
  .icon-rule__line { flex: 1; height: 1.5px; background: var(--orange); }
  .icon-rule__icons { display: flex; gap: 8px; }
  .icon {
    width: 27px; height: 27px;
    background: var(--orange);
    border-radius: 4px;
    display: flex; align-items: center; justify-content: center;
  }
  .icon svg { width: 17px; height: 17px; }

  .contact {
    position: absolute;
    top: 520px; left: 0; right: 0;
    list-style: none;
    font-size: 19px;
    line-height: 1.45;
  }
  .contact__note { color: var(--orange); font-size: 15px; }

  .services {
    position: absolute;
    top: 430px; left: 0; right: 0;
    list-style: none;
    font-size: 27px;
    line-height: 1.4;
  }
  .services li::before {
    content: "";
    display: inline-block;
    width: 8px; height: 8px;
    border-radius: 50%;
    background: var(--orange);
    margin-right: 9px;
    vertical-align: 12px;
  }
</style>
</head>
<body>

<section class="card card--front">
  <div class="brand"><span class="brand__mark"></span>Harrow Grading LLC</div>

  <div class="person">
    <div class="person__name">Dellan Price</div>
    <div class="person__role">Founder</div>
  </div>

  <div class="icon-rule">
    <span class="icon-rule__line"></span>
    <div class="icon-rule__icons">
      <span class="icon"><svg viewBox="0 0 24 24" fill="#fff"><path d="M6.6 10.8a15.1 15.1 0 0 0 6.6 6.6l2.2-2.2c.3-.3.7-.4 1-.2 1.1.4 2.3.6 3.6.6.6 0 1 .4 1 1V20c0 .6-.4 1-1 1A17 17 0 0 1 3 4c0-.6.4-1 1-1h3.5c.6 0 1 .4 1 1 0 1.3.2 2.5.6 3.6.1.3 0 .7-.2 1z"/></svg></span>
      <span class="icon"><svg viewBox="0 0 24 24" fill="none" stroke="#fff" stroke-width="2"><rect x="7" y="2.5" width="10" height="19" rx="2"/><line x1="11" y1="18" x2="13" y2="18"/></svg></span>
      <span class="icon"><svg viewBox="0 0 24 24" fill="none" stroke="#fff" stroke-width="2"><rect x="3" y="5.5" width="18" height="13" rx="1"/><path d="M3 6l9 7 9-7"/></svg></span>
      <span class="icon"><svg viewBox="0 0 24 24" fill="none" stroke="#fff" stroke-width="2"><circle cx="12" cy="12" r="9"/><path d="M3 12h18M12 3c3 3 3 15 0 18M12 3c-3 3-3 15 0 18"/></svg></span>
    </div>
    <span class="icon-rule__line"></span>
  </div>

  <ul class="contact">
    <li>208-319-4856 <span class="contact__note">(office)</span></li>
    <li>208-417-6290</li>
    <li>harrowgradingllc@maplecove.com</li>
    <li>www.harrowgradingllc.com</li>
  </ul>
</section>

<section class="card card--back">
  <div class="brand"><span class="brand__mark"></span>Harrow Grading LLC</div>

  <ul class="services">
    <li>Driveways</li>
    <li>Site Prep</li>
    <li>Retaining Walls</li>
    <li>Septic Systems</li>
    <li>Rock Delivery</li>
  </ul>
</section>

</body>
</html>
```